New Business Card Design Project

Use the flyer uploaded and website www.brightoakbuilders.com for inspiration.
List Our Services on Backside of business cards
Marcus Delling
Harborline Builders Inc.
Licensed General Contractors
858-471-6093

Contact Information for Business Card

Use the flyer uploaded and website www.brightoakbuilders.com for inspiration. List Our Services on Backside of business cards Marcus Delling Harborline Builders Inc. Licensed General Contractors 858-471-6093

```html
<!DOCTYPE html>
<html lang="en">
<head>
<meta charset="utf-8">
<title>Harborline Builders – Business Card</title>
<link href="https://fonts.googleapis.com/css2?family=Montserrat:wght@400;500;700&display=swap" rel="stylesheet">
<style>
  :root {
    --backdrop: #a4a8a9;
    --card: #141414;
    --ink: #f4f4f4;
    --ink-soft: #e2e2e2;
  }
  * { margin: 0; padding: 0; box-sizing: border-box; }
  html, body {
    width: 1179px; height: 1200px; overflow: hidden;
    background: var(--backdrop);
    font-family: "Montserrat", sans-serif;
    color: var(--ink);
  }
  .card {
    position: absolute;
    left: 222px;
    width: 736px;
    height: 422px;
    background: var(--card);
  }
  .card--back { top: 162px; }
  .card--front { top: 620px; left: 221px; }

  .brand {
    position: absolute;
    display: flex;
    justify-content: center;
    align-items: center;
    gap: 8px;
    font-weight: 500;
    font-size: 17px;
    letter-spacing: 0.04em;
    color: var(--ink);
    white-space: nowrap;
  }
  .brand__dot {
    width: 10px; height: 10px;
    border: 1.5px solid var(--ink);
    border-radius: 50%;
    flex: none;
  }
  .card--back .brand { left: 50px; width: 277px; top: 214px; }
  .card--front .brand { left: 418px; width: 277px; top: 86px; }

  .divider {
    position: absolute;
    left: 355px; top: 105px;
    width: 1.5px; height: 250px;
    background: var(--ink);
  }
  .services {
    position: absolute;
    left: 382px; top: 100px;
  }
  .services__title {
    font-weight: 700;
    font-size: 21px;
    margin-bottom: 8px;
  }
  .services__list { list-style: none; }
  .services__list li {
    font-size: 16.5px;
    line-height: 25.4px;
    color: var(--ink-soft);
    position: relative;
    padding-left: 13px;
  }
  .services__list li::before {
    content: "";
    position: absolute;
    left: 0; top: 10px;
    width: 6px; height: 6px;
    border-radius: 50%;
    background: var(--ink);
  }

  .person { position: absolute; left: 40px; top: 45px; }
  .person__name { font-weight: 700; font-size: 27px; line-height: 32px; }
  .person__role { font-size: 16px; color: var(--ink-soft); }

  .contact {
    position: absolute; left: 37px; top: 274px;
    list-style: none;
  }
  .contact li {
    display: flex; align-items: center; gap: 13px;
    font-size: 16px; line-height: 27.5px;
    color: var(--ink-soft);
  }
  .contact svg { width: 15px; height: 15px; fill: var(--ink); flex: none; }

  .license {
    position: absolute; left: 35px; top: 371px;
    font-size: 16px; color: var(--ink-soft);
  }
  .address {
    position: absolute; left: 449px; top: 352px;
    font-size: 16.5px; line-height: 19px; color: var(--ink-soft);
  }
</style>
</head>
<body>

<section class="card card--back">
  <div class="brand"><span class="brand__dot"></span>HARBORLINE BUILDERS</div>
  <div class="divider"></div>
  <div class="services">
    <h2 class="services__title">Our Services</h2>
    <ul class="services__list">
      <li>Remodel: Kitchen &amp; Bath</li>
      <li>Painting: Interior &amp; Exterior</li>
      <li>Flooring: Carpet, Vinyl, Wood</li>
      <li>Window &amp; Door Replacement</li>
      <li>Plumbing: Repair &amp; Upgrades</li>
      <li>Energy Efficienct Upgrades</li>
      <li>Deck &amp; Patio construction</li>
      <li>Water &amp; Mold Damage</li>
      <li>Garage Renovation</li>
    </ul>
  </div>
</section>

<section class="card card--front">
  <div class="person">
    <h1 class="person__name">Marcus Delling</h1>
    <p class="person__role">Managing Director</p>
  </div>
  <div class="brand"><span class="brand__dot"></span>HARBORLINE BUILDERS</div>

  <ul class="contact">
    <li>
      <svg viewBox="0 0 16 16" aria-hidden="true"><path d="M1 5c0-2 3-3 7-3s7 1 7 3v1.5h-3.5V5H4.5v1.5H1z"/><path d="M3 8l2-2h6l2 2v6H3z"/><circle cx="8" cy="10.5" r="1.6" fill="#141414"/></svg>
      <span>858-471-6093</span>
    </li>
    <li>
      <svg viewBox="0 0 16 16" aria-hidden="true"><path d="M1 3h14v1.2L8 9 1 4.2z"/><path d="M1 5.8 8 10.6l7-4.8V13H1z"/></svg>
      <span>info@brightoakbuilders.com</span>
    </li>
    <li>
      <svg viewBox="0 0 16 16" aria-hidden="true"><circle cx="8" cy="8" r="7"/><path d="M4 4.5c1.5 0 2 1 3 1s.5 2-1 2.5-1 2-2 2.5-2-1.5-2-3 1-3 2-3zM10 9c1.5 0 2.5.5 2 2s-2 2.5-3 2-.5-4 1-4z" fill="#141414"/></svg>
      <span>www.brightoakbuilders.com</span>
    </li>
  </ul>

  <p class="license">CLSB Licensed No #1084526</p>
  <p class="address">48 Larkfield Road, suite 210<br>Dunmore PA 18512</p>
</section>

</body>
</html>
```